website refresh/redesign needed for Printing e commerce website

We'd like a website refresh/redesign done with the specific goal of having the site act as a more effective funnel for leads.<br/><br/>We think that the current design is outdated.<br/><br/>We want our customers and partners to still recognize the website, Is a big chunk of our business is repeat orders. <br/>so it should not be a full redesign. General color scheme and such should remain the same so that it is clear we are the same company. <br/><br/>However, the updated website design should look more polished and convey high-quality products and services that we provide. <br/><br/>Our website is https://shopledgerslipsnet.paperformdepot.example/ if you want to take a look at our current website design. <br/><br/>we need 3 pages redesigned... <br/><br/>1. homepage:https://shopledgerslipsnet.paperformdepot.example/<br/><br/>2. Category page: <br/>https://shopledgerslipsnet.paperformdepot.example/order-computer-checks-c-4.html<br/><br/>3. Product detail page: https://shopledgerslipsnet.paperformdepot.example/voucher-computer-checks-p-35.html<br/><br/> I can provide many more pictures of our products if needed.<br/><br/><br/>BTW. I have another project here on mural hive, you can check the other ones too, so to make it easier to do both when working on this.<br/><br/> Please reach out to me should you have any questions or comments.
3 page
Designer to choose colors to be used in the design.

```html
<!DOCTYPE html>
<html lang="en">
<head>
<meta charset="utf-8">
<title>LedgerSlipDepot – Business Checks</title>
<link href="https://fonts.googleapis.com/css2?family=Roboto:ital,wght@0,400;0,500;0,700;1,400&display=swap" rel="stylesheet">
<style>
:root{
  --header:#275012;
  --forest:#1f4a0e;
  --heading:#1d4a0c;
  --lime:#52e23a;
  --price:#2aa51a;
  --teal:#1a8a9c;
  --promo-grey:#f3f3f3;
  --promo-green:#d5f5cf;
  --ink:#222;
  --soft-name:#2e4b86;
  --footer:#3b3b3b;
  --white:#fff;
}
*{box-sizing:border-box;margin:0;padding:0}
html,body{width:1200px;height:3220px;overflow:hidden}
body{font-family:"Roboto",Arial,sans-serif;color:var(--ink);background:var(--white);position:relative}
.abs{position:absolute}
.center{text-align:center}

/* header */
.topbar{left:0;top:0;width:1200px;height:70px;background:var(--header)}
.brand{left:174px;top:24px;color:var(--white);font-weight:700;font-size:17px;display:flex;align-items:center;gap:8px}
.brand-dot{width:10px;height:10px;background:var(--lime)}
.search{left:470px;top:20px;width:330px;height:26px;border-bottom:1px solid #9bb38f;color:var(--white);font-size:11px;padding:6px 6px}
.search svg{position:absolute;right:4px;top:7px}
.header-icons{left:938px;top:22px;display:flex;gap:14px}
.cart-count{left:1016px;top:21px;width:12px;height:12px;border-radius:50%;background:var(--white);color:var(--header);font-size:8px;font-weight:700;text-align:center;line-height:12px}

.nav{left:0;top:70px;width:1200px;height:62px;background:var(--white);border-bottom:1px solid #eee}
.nav ul{list-style:none;display:flex;position:absolute;left:181px;top:26px}
.nav li{font-size:12px;font-weight:500;color:#222;margin-right:44px;position:relative}
.nav li.active::after{content:"";position:absolute;left:-4px;bottom:-23px;width:40px;height:3px;background:var(--lime)}

/* hero */
.hero{left:0;top:132px;width:1200px;height:553px;background:linear-gradient(135deg,#1a7d90,#1d95a8 55%,#157585)}
.hero-art{left:700px;top:210px;width:415px;height:415px;background:linear-gradient(135deg,#e6dbf0,#d6f1ea);opacity:.85;border-radius:4px}
.hero-offer{left:180px;top:298px;width:520px;font-size:44px;font-weight:700;color:var(--lime)}
.hero-title{left:180px;top:350px;width:520px;font-size:48px;font-weight:700;color:var(--white)}
.hero-btn{left:347px;top:428px;width:158px;height:47px;border:3px solid var(--lime);border-radius:24px;background:var(--teal);color:var(--white);font-weight:700;font-size:16px;line-height:41px}
.hero-arrow{top:373px;width:48px;height:72px;background:rgba(0,0,0,.12)}

/* promos */
.promo-panel{top:704px;height:287px}
.promo-art{top:770px;width:205px;height:155px;background:linear-gradient(180deg,#e8eaf6,#dfe6f2);border-radius:3px}
.promo-text{top:762px}
.promo-pct{font-size:40px;font-weight:700;color:var(--price)}
.promo-name{font-size:24px;font-weight:500;color:#444;margin-top:2px}
.promo-text ul{list-style:none;margin-top:14px;font-size:14px;color:#555;line-height:26px}
.promo-text li::before{content:"• "}

/* section headings */
.sec-title{left:0;width:1200px;font-size:33px;font-weight:700;color:var(--heading)}

/* category cards */
.card{top:1137px;height:388px;background:var(--white);box-shadow:0 1px 6px rgba(0,0,0,.15)}
.card.featured{box-shadow:0 0 20px rgba(82,226,58,.45)}
.card-art{position:absolute;left:50%;top:24px;width:150px;height:138px;transform:translateX(-50%);background:linear-gradient(135deg,#d8e7f7,#eef1f6)}
.card h3{position:absolute;top:190px;width:100%;font-size:15px;font-weight:500;color:#111}
.card p{position:absolute;top:226px;width:100%;font-size:12px;color:#555;line-height:22px}
.card .price{position:absolute;top:278px;width:100%;font-size:17px;font-weight:700;color:var(--price)}
.card .btn{position:absolute;left:50%;top:328px;transform:translateX(-50%);width:120px;height:34px;border:2px solid var(--lime);border-radius:18px;font-size:13px;font-weight:700;color:var(--price);line-height:30px}

/* best seller */
.bestseller{left:0;top:1597px;width:1200px;height:535px;background:var(--forest)}
.tile{top:1760px;width:181px;height:200px;border:3px solid var(--lime);background:var(--white);box-shadow:0 0 10px rgba(82,226,58,.5)}
.tile-art{position:absolute;left:24px;top:22px;width:128px;height:150px;background:linear-gradient(180deg,#dfe9f7,#e4f2e2)}
.tile-name{top:1985px;width:181px;color:var(--white);font-size:14px;font-weight:500;line-height:18px}
.tile-price{top:2030px;width:181px;color:var(--lime);font-size:18px;font-weight:700}

/* testimonials */
.quote{top:2263px;width:271px;height:169px;border:2px solid #c5f1bd;background:var(--white)}
.quote p{position:absolute;left:28px;top:18px;width:225px;font-size:12px;font-style:italic;color:#555;line-height:24px;white-space:nowrap}
.quote .mark{position:absolute;right:16px;top:112px;font-size:60px;color:#ddd;line-height:1;font-weight:700;font-family:Georgia,serif}
.quote .tail{position:absolute;left:48px;bottom:-17px}
.avatar{top:2470px;width:64px;height:64px;border-radius:50%;background:linear-gradient(135deg,#d9c9bd,#a9b7c7)}
.stars{font-size:11px;color:#888;letter-spacing:1px}
.reviewer{font-size:14px;font-weight:500;color:#111}

/* software */
.soft-row{left:170px;top:2755px;width:860px;display:flex;justify-content:space-between;align-items:center;height:40px}
.soft-row span{font-size:24px;font-weight:700;color:var(--soft-name)}
.soft-arrow{top:2760px}

/* footer */
.footer{left:0;top:2880px;width:1200px;height:340px;background:var(--footer)}
.fcol h4{font-size:14px;font-weight:700;color:var(--white);margin-bottom:20px}
.fcol ul{list-style:none;font-size:13px;color:#eee;line-height:26px}
.email{left:760px;top:2983px;width:265px;height:35px;border:2px solid var(--lime);color:#ddd;font-size:13px;padding:8px 14px}
.subscribe{left:760px;top:3043px;width:118px;height:35px;border-radius:18px;background:var(--lime);color:var(--forest);font-size:14px;font-weight:700;text-align:center;line-height:35px}
.paycards{left:760px;top:3090px;display:flex;gap:10px}
.paycards span{width:38px;height:22px;background:#f0f0f0;border-radius:2px;font-size:7px;font-weight:700;color:#333;text-align:center;line-height:22px}
.rule{left:172px;top:3160px;width:856px;height:1px;background:#595959}
.copy{left:175px;top:3183px;font-size:12px;color:#eee}
.social{left:805px;top:3170px;display:flex;gap:6px}
.social span{width:40px;height:40px;border:2px solid var(--white);border-radius:50%;color:var(--white);font-size:7px;text-align:center;line-height:36px}
</style>
</head>
<body>

<div class="abs topbar"></div>
<div class="abs brand"><span class="brand-dot"></span>LedgerSlipDepot</div>
<div class="abs search">Enter keyword
  <svg width="10" height="10" viewBox="0 0 10 10"><circle cx="4" cy="4" r="3" fill="none" stroke="#fff" stroke-width="1.5"/><path d="M6.3 6.3 9 9" stroke="#fff" stroke-width="1.5"/></svg>
</div>
<div class="abs header-icons">
  <svg width="18" height="18" viewBox="0 0 24 24"><path d="M12 21 4 13a5 5 0 0 1 8-6 5 5 0 0 1 8 6z" fill="none" stroke="#52e23a" stroke-width="2"/></svg>
  <svg width="18" height="18" viewBox="0 0 24 24"><circle cx="12" cy="12" r="10" fill="none" stroke="#52e23a" stroke-width="2"/><circle cx="12" cy="10" r="3.5" fill="none" stroke="#52e23a" stroke-width="2"/><path d="M6 19c2-4 10-4 12 0" fill="none" stroke="#52e23a" stroke-width="2"/></svg>
  <svg width="18" height="18" viewBox="0 0 24 24"><path d="M5 8h14l-1 13H6z M9 8V5a3 3 0 0 1 6 0v3" fill="none" stroke="#52e23a" stroke-width="2"/></svg>
</div>
<div class="abs cart-count">0</div>

<nav class="abs nav">
  <ul>
    <li class="active">HOME</li>
    <li>BUSINESS CHECKS</li>
    <li>COMPUTER CHECKS</li>
    <li>LEDGERBOOKS CHECKS</li>
    <li>ACCESSORIES</li>
    <li>HELP/FAQS</li>
    <li>REORDER</li>
  </ul>
</nav>

<div class="abs hero" role="img" aria-label="Holiday backdrop with pine branches, ornaments and a gift box"></div>
<div class="abs hero-art" role="img" aria-label="Two business checks fanned out"></div>
<div class="abs hero-offer center">GET 50% OFF</div>
<div class="abs hero-title center">Business Checks</div>
<div class="abs hero-btn center">ORDER NOW</div>
<div class="abs hero-arrow" style="left:0">
  <svg width="48" height="72" viewBox="0 0 48 72"><path d="M30 22 16 36l14 14" fill="none" stroke="#fff" stroke-width="2"/></svg>
</div>
<div class="abs hero-arrow" style="left:1152px">
  <svg width="48" height="72" viewBox="0 0 48 72"><path d="M18 22l14 14-14 14" fill="none" stroke="#fff" stroke-width="2"/></svg>
</div>

<div class="abs promo-panel" style="left:0;width:591px;background:var(--promo-grey)"></div>
<div class="abs promo-art" style="left:62px" role="img" aria-label="Stack of computer checks"></div>
<div class="abs promo-text" style="left:310px">
  <div class="promo-pct">20% OFF</div>
  <div class="promo-name">COMPUTER CHECKS</div>
  <ul><li>100% software Compatible</li><li>Ships within 24hr</li><li>Free logo</li></ul>
</div>
<div class="abs promo-panel" style="left:608px;width:592px;background:var(--promo-green)"></div>
<div class="abs promo-art" style="left:665px" role="img" aria-label="Three-per-page manual checks"></div>
<div class="abs promo-text" style="left:918px">
  <div class="promo-pct">30% OFF</div>
  <div class="promo-name">&nbsp;MANUAL CHECKS</div>
  <ul><li>Fits for 7 ring binder</li><li>Ships within 24hr</li><li>Free logo</li></ul>
</div>

<h2 class="abs sec-title center" style="top:1052px">ORDER BUSINESS CHECKS</h2>

<div class="abs card center" style="left:171px;width:258px">
  <div class="card-art" role="img" aria-label="Voucher checks with security seal"></div>
  <h3>LEDGERBOOKS CHECKS</h3>
  <p>Voucher Checks - 3 Per Page - wallet<br>Order custom designed LedgerBooks</p>
  <div class="price">Starts at $12.99</div>
  <div class="btn">READ MORE</div>
</div>
<div class="abs card featured center" style="left:472px;width:256px">
  <div class="card-art" role="img" aria-label="Colored deposit slip pads"></div>
  <h3>DEPOSIT SLIPS</h3>
  <p>Voucher Checks - 3 Per Page - wallet<br>Order custom designed LedgerBooks</p>
  <div class="price">Starts at $12.99</div>
  <div class="btn">READ MORE</div>
</div>
<div class="abs card center" style="left:766px;width:258px">
  <div class="card-art" role="img" aria-label="Security window envelopes"></div>
  <h3>ACCESSORIES</h3>
  <p>Voucher Checks - 3 Per Page - wallet<br>Order custom designed LedgerBooks</p>
  <div class="price">Starts at $12.99</div>
  <div class="btn">READ MORE</div>
</div>

<div class="abs bestseller"></div>
<h2 class="abs sec-title center" style="top:1655px;color:var(--white)">BEST SELLER</h2>
<svg class="abs" style="left:100px;top:1845px" width="24" height="40" viewBox="0 0 24 40"><path d="M20 2 4 20l16 18" fill="none" stroke="#fff" stroke-width="2"/></svg>
<svg class="abs" style="left:1064px;top:1845px" width="24" height="40" viewBox="0 0 24 40"><path d="M4 2l16 18L4 38" fill="none" stroke="#fff" stroke-width="2"/></svg>

<div class="abs tile" style="left:172px"><div class="tile-art" role="img" aria-label="Blue voucher check"></div></div>
<div class="abs tile" style="left:396px"><div class="tile-art" role="img" aria-label="Green three-per-page checks"></div></div>
<div class="abs tile" style="left:621px"><div class="tile-art" role="img" aria-label="Security voucher checks"></div></div>
<div class="abs tile" style="left:845px"><div class="tile-art" role="img" aria-label="Multicolor business checks"></div></div>
<div class="abs tile-name center" style="left:172px">LedgerBooks<br>Voucher Checks</div>
<div class="abs tile-name center" style="left:396px">LedgerBooks<br>Voucher Checks</div>
<div class="abs tile-name center" style="left:621px">LedgerBooks<br>Voucher Checks</div>
<div class="abs tile-name center" style="left:845px">LedgerBooks<br>Voucher Checks</div>
<div class="abs tile-price center" style="left:172px">From $12.99</div>
<div class="abs tile-price center" style="left:396px">From $12.99</div>
<div class="abs tile-price center" style="left:621px">From $12.99</div>
<div class="abs tile-price center" style="left:845px">From $12.99</div>

<h2 class="abs sec-title center" style="top:2183px">WHAT OUR CUSTOMERS SAY</h2>

<div class="abs quote" style="left:173px">
  <p>Lorem ipsum dolor sit amet, conse<br>ctetur adipiscing elit, sed do eiusmod<br>tempor incididunt ut labore et dolore<br>magna aliqua. Ut enim ad minim ven<br>iam, quis nostrud exercitatio</p>
  <span class="mark">“</span>
  <svg class="tail" width="36" height="18" viewBox="0 0 36 18"><path d="M0 0 18 17 36 0" fill="#fff" stroke="#c5f1bd" stroke-width="2"/></svg>
</div>
<div class="abs quote" style="left:465px">
  <p>Lorem ipsum dolor sit amet, conse<br>ctetur adipiscing elit, sed do eiusmod<br>tempor incididunt ut labore et dolore<br>magna aliqua. Ut enim ad minim ven<br>iam, quis nostrud exercitatio</p>
  <span class="mark">“</span>
  <svg class="tail" width="36" height="18" viewBox="0 0 36 18"><path d="M0 0 18 17 36 0" fill="#fff" stroke="#c5f1bd" stroke-width="2"/></svg>
</div>
<div class="abs quote" style="left:756px">
  <p>Lorem ipsum dolor sit amet, conse<br>ctetur adipiscing elit, sed do eiusmod<br>tempor incididunt ut labore et dolore<br>magna aliqua. Ut enim ad minim ven<br>iam, quis nostrud exercitatio</p>
  <span class="mark">“</span>
  <svg class="tail" width="36" height="18" viewBox="0 0 36 18"><path d="M0 0 18 17 36 0" fill="#fff" stroke="#c5f1bd" stroke-width="2"/></svg>
</div>

<div class="abs avatar" style="left:200px" role="img" aria-label="Customer portrait"></div>
<div class="abs" style="left:274px;top:2474px"><div class="stars">★★★★★</div><div class="reviewer">Name,Cty NAme</div></div>
<div class="abs avatar" style="left:492px" role="img" aria-label="Customer portrait"></div>
<div class="abs" style="left:566px;top:2474px"><div class="stars">★★★★★</div><div class="reviewer">Name,Cty NAme</div></div>
<div class="abs avatar" style="left:783px" role="img" aria-label="Customer portrait"></div>
<div class="abs" style="left:857px;top:2474px"><div class="stars">★★★★★</div><div class="reviewer">Name,Cty NAme</div></div>

<h2 class="abs sec-title center" style="top:2656px">CHECKS BY SOFTWARE</h2>
<svg class="abs soft-arrow" style="left:134px" width="20" height="34" viewBox="0 0 20 34"><path d="M16 2 4 17l12 15" fill="none" stroke="#999" stroke-width="2"/></svg>
<svg class="abs soft-arrow" style="left:1060px" width="20" height="34" viewBox="0 0 20 34"><path d="M4 2l12 15L4 32" fill="none" stroke="#999" stroke-width="2"/></svg>
<div class="abs soft-row">
  <span>Ferncount</span>
  <span>LedgerBooks</span>
  <span>Cardamom</span>
  <span>Quillfund</span>
  <span>Northgate Ledger</span>
</div>

<footer class="abs footer"></footer>
<div class="abs fcol" style="left:172px;top:2948px"><h4>INFO</h4><ul><li>Contact us</li><li>Order History</li><li>Track Order</li><li>Help &amp; Support</li></ul></div>
<div class="abs fcol" style="left:348px;top:2948px"><h4>SUPPORT</h4><ul><li>Contact Us</li><li>Shipping &amp; Turnaround</li><li>Help FAQs</li><li>Order Status</li><li>Reorder</li></ul></div>
<div class="abs fcol" style="left:559px;top:2948px"><h4>INFORMATION</h4><ul><li>About Us</li><li>Privacy &amp; Security</li><li>Refunds &amp; Returns</li><li>Terms &amp; Conditions</li><li>Rush Order</li></ul></div>
<div class="abs fcol" style="left:760px;top:2948px"><h4>NEWSLETER SIGN UP</h4></div>
<div class="abs email">Email address</div>
<div class="abs subscribe">SUBSCRIBE</div>
<div class="abs paycards"><span>Velloro</span><span>Amberline</span><span>Farquay</span><span>Orbicard</span><span>Quelpay</span></div>
<div class="abs rule"></div>
<div class="abs copy">Copyright © 2019 LedgerSlipDepot.example. | Sitemap</div>
<div class="abs social"><span>Chirp</span><span>Facet</span><span>Linkr</span><span>Plusone</span><span>Snapgram</span></div>

</body>
</html>
```